American cannabis tech company business card design

Pavrel.com is seeking a modern, professional, and brand-aligned business card that represents our company and its core values: Mission, Story, Values, and Impact. As an innovative cannabis company, we want a business card that is not only visually appealing but also serves as a representation of who we are and what we stand for.

Project Scope: Design a double-sided business card that integrates our brand identity and core values. Incorporate our key brand elements, ensuring a sleek and contemporary aesthetic. Visually reflect our core values (Mission, Story, Values, Impact) in a way that is engaging yet professional.

Target Market(s)

Vendors, third parties,

Contact Information for Business Card

Contact details (name, title, email, phone, website, etc.)

Font styles to use
Other font styles liked:
• Caslon, Centra

Colors

Designer to choose colors to be used in the design.

Requirements
Must have
• Pavrel.com logo and branding A creative yet clean way to integrate our core values (Mission, Story, Values, Impact) Modern typography and a well-structured layout
Nice to have
• forest green, grey, white, black
Should not have
• references to marijuana, leafs, plants, or related product

```html
<!DOCTYPE html>
<html lang="en">
<head>
<meta charset="utf-8">
<title>Pavrel.com Business Card</title>
<link href="https://fonts.googleapis.com/css2?family=Poppins:wght@300;400;600;800&display=swap" rel="stylesheet">
<style>
  :root {
    --backdrop: #1d1d1e;
    --forest: #17321a;
    --forest-deep: #0f2412;
    --forest-bright: #2f7a3a;
    --white: #ffffff;
    --rule: #6f8a72;
  }
  * { margin: 0; padding: 0; box-sizing: border-box; }
  html, body {
    width: 1200px;
    height: 1108px;
    overflow: hidden;
    background: var(--backdrop);
    font-family: "Poppins", sans-serif;
    color: var(--white);
  }
  .stage {
    position: relative;
    width: 1200px;
    height: 1108px;
  }
  .card {
    position: absolute;
    top: 244px;
    width: 370px;
    height: 620px;
    border-radius: 22px;
    background: var(--forest);
    overflow: hidden;
  }
  .card--front { left: 185px; }
  .card--back { left: 645px; }

  .front-wordmark {
    position: absolute;
    top: 92px;
    left: 0;
    width: 100%;
    text-align: center;
    font-weight: 800;
    font-size: 76px;
    letter-spacing: 1px;
    line-height: 1;
  }
  .identity {
    position: absolute;
    top: 388px;
    width: 100%;
    text-align: center;
  }
  .identity__name {
    font-weight: 600;
    font-size: 27px;
    letter-spacing: 0.5px;
    line-height: 1.1;
  }
  .identity__title {
    font-weight: 400;
    font-size: 16px;
    letter-spacing: 1px;
    margin-top: 2px;
  }
  .contact-icons {
    position: absolute;
    top: 466px;
    left: 30px;
    right: 30px;
    display: flex;
    align-items: center;
    gap: 8px;
  }
  .contact-icons__rule {
    flex: 1;
    height: 1px;
    background: var(--rule);
  }
  .contact-icons__box {
    width: 34px;
    height: 34px;
    border-radius: 5px;
    background: var(--white);
    display: flex;
    align-items: center;
    justify-content: center;
  }
  .contact-list {
    position: absolute;
    top: 516px;
    width: 100%;
    list-style: none;
    text-align: center;
    font-weight: 400;
    font-size: 19px;
    line-height: 1.4;
  }

  .back-texture {
    position: absolute;
    inset: 0;
    background:
      radial-gradient(ellipse at 85% 10%, var(--forest-bright) 0%, rgba(47,122,58,0) 55%),
      linear-gradient(160deg, var(--forest) 0%, var(--forest-deep) 100%);
  }
  .back-wordmark {
    position: absolute;
    top: 430px;
    left: 0;
    width: 100%;
    text-align: center;
    font-weight: 800;
    font-size: 30px;
    letter-spacing: 0.5px;
  }
</style>
</head>
<body>
<main class="stage">
  <section class="card card--front" aria-label="Business card front">
    <div class="front-wordmark">PAVREL</div>
    <div class="identity">
      <h1 class="identity__name">DANIEL HART</h1>
      <p class="identity__title">MANAGING DIRECTOR</p>
    </div>
    <div class="contact-icons">
      <span class="contact-icons__rule"></span>
      <span class="contact-icons__box" aria-label="Phone">
        <svg width="22" height="22" viewBox="0 0 24 24"><path fill="#17321a" d="M6.6 10.8a15 15 0 0 0 6.6 6.6l2.2-2.2c.3-.3.7-.4 1-.2 1.1.4 2.3.6 3.6.6.6 0 1 .4 1 1V20c0 .6-.4 1-1 1A17 17 0 0 1 3 4c0-.6.4-1 1-1h3.5c.6 0 1 .4 1 1 0 1.3.2 2.5.6 3.6.1.3 0 .7-.2 1z"/></svg>
      </span>
      <span class="contact-icons__box" aria-label="Email">
        <svg width="22" height="22" viewBox="0 0 24 24"><rect x="3" y="6" width="18" height="12" rx="1" fill="#17321a"/><path d="M3.5 6.5 12 13l8.5-6.5M3.5 17.5l6.5-5.5M20.5 17.5 14 12" stroke="#fff" stroke-width="1.2" fill="none"/></svg>
      </span>
      <span class="contact-icons__box" aria-label="Website">
        <svg width="22" height="22" viewBox="0 0 24 24"><circle cx="12" cy="12" r="9" fill="#17321a"/><path d="M3 12h18M12 3c3 3 3 15 0 18M12 3c-3 3-3 15 0 18" stroke="#fff" stroke-width="1.2" fill="none"/></svg>
      </span>
      <span class="contact-icons__rule"></span>
    </div>
    <ul class="contact-list">
      <li>044-555 010 234</li>
      <li>info@pavrel.com</li>
      <li>www.pavrel.com</li>
    </ul>
  </section>

  <section class="card card--back" aria-label="Business card back">
    <div class="back-texture" role="img" aria-label="Repeating brand name pattern in tonal green, glossy toward the top right"></div>
    <div class="back-wordmark">PAVREL</div>
  </section>
</main>
</body>
</html>
```